Kestrova - presentation for a remote DBA team offering data platform management

We need a website design for wordpress site called Kestrova.cz
We deliver remote database and data platform administration and development, oversee the database administrators, consult and train the personnel responsible for the database operations. The website should include several sections, home page with graphics elements supporting the name and service - remote dba work; blog section; service introduction and description, team introduction and description, download section for documents, presentations etc.

Target Market(s)

small and medium business companies requiring remote DBA service

Number of Pages Required

3 page

Font styles to use
Sans Serif

Colors

Designer to choose colors to be used in the design.

Requirements
Must have
• The website should have several sections to introduce the services, blog, team introduction, downloads

```html
<!DOCTYPE html>
<html lang="en">
<head>
<meta charset="utf-8">
<title>Kestrova – Remote DBA Team</title>
<link rel="stylesheet" href="https://fonts.googleapis.com/css2?family=Open+Sans:wght@400;600;700;800&display=swap">
<style>
:root{
  --blue:#1c22a8;
  --blue-bright:#2b3bd8;
  --navy:#0a0e5a;
  --ink:#1b1b1b;
  --muted:#6d6d6d;
  --light:#ececec;
  --faint:#e9e9ee;
  --white:#ffffff;
  --footer-bar:#7a7a7a;
}
*{box-sizing:border-box;margin:0;padding:0}
html,body{width:1200px;height:3396px;overflow:hidden;background:var(--white);font-family:"Open Sans",sans-serif;color:var(--ink)}
.page{position:relative;width:1200px;height:3396px;overflow:hidden}
.abs{position:absolute}
p{line-height:1.7}

/* header */
.site-header{left:0;top:0;width:1200px;height:110px;background:var(--white);z-index:3}
.brand{left:74px;top:30px;font-size:36px;font-weight:700;color:#4a4a4a;letter-spacing:.5px}
.nav{right:72px;top:36px;display:flex;align-items:center;gap:38px;font-size:15px;font-weight:600;text-transform:uppercase}
.nav-home{width:40px;height:40px;background:var(--blue);display:flex;align-items:center;justify-content:center}

/* hero */
.hero{left:0;top:110px;width:1200px;height:570px;background:linear-gradient(120deg,#0c1590 0%,#2a47e0 45%,#1a2fb8 70%,#3b5cf0 100%);clip-path:polygon(0 0,100% 0,100% 90%,0 100%)}
.hero-panel{left:216px;top:294px;width:792px;height:234px;background:rgba(20,30,110,.55);border:1px solid rgba(255,255,255,.35);text-align:center;color:var(--white)}
.hero-panel h1{font-size:29px;font-weight:700;margin-top:28px}
.hero-panel p{font-size:15px;width:640px;margin:16px auto 0;line-height:1.8;color:#e4e7ff}
.btn{display:inline-flex;align-items:center;gap:14px;font-size:14px;font-weight:700;text-transform:uppercase;color:var(--white);padding:0 22px;height:38px}
.btn-grey{background:#5d5d64;margin-top:14px}
.btn-blue{background:var(--blue)}
.arrow{left:118px;top:372px}
.arrow-r{right:118px;top:372px}

/* stats band */
.stats{left:0;top:620px;width:1200px;height:229px;background:var(--light);z-index:-1}
.stats-title{left:68px;top:690px;font-size:30px;font-weight:700;line-height:1.35;text-transform:uppercase}
.stats-title b{font-size:52px;color:var(--navy);font-weight:800}
.stats-dot{left:464px;top:743px;width:30px;height:30px;border-radius:50%;background:var(--blue)}
.stats-text{left:503px;top:706px;width:630px;font-size:15px;color:#333;line-height:1.6}

/* about */
.ghost{font-weight:800;color:var(--faint);text-transform:uppercase}
.about-ghost{left:82px;top:850px;font-size:74px}
.about-title{left:80px;top:920px;font-size:26px;text-transform:uppercase}
.rule{height:3px;width:60px;background:var(--blue)}
.rule::after{content:"";display:block;width:20px;height:3px;margin-left:64px;background:var(--blue)}
.about-lead{left:76px;top:988px;width:520px;font-size:15px;font-weight:700;line-height:1.6}
.about-body{left:76px;top:1056px;width:520px;font-size:13px;color:var(--muted)}
.service{width:250px}
.service svg{display:block;margin-bottom:8px}
.service h3{font-size:16px;font-weight:700;line-height:1.4;margin-bottom:6px}
.service p{font-size:13px;color:var(--muted);line-height:1.65}

/* team */
.team{left:0;top:1268px;width:1200px;height:602px;background:linear-gradient(135deg,#1d2ab5 0%,#2840d6 50%,#1420a0 100%);clip-path:polygon(0 9%,100% 0,100% 93%,0 100%)}
.team-ghost{left:0;width:1200px;top:1310px;text-align:center;font-size:60px;color:rgba(255,255,255,.14)}
.team-title{left:0;width:1200px;top:1384px;text-align:center;font-size:24px;font-weight:700;color:var(--white)}
.portrait{border-radius:50%;border:4px solid var(--white);background:linear-gradient(160deg,#c8b4a2,#6a5a52)}
.team-text{left:262px;top:1630px;width:676px;text-align:center;font-size:14px;color:#dfe3ff}

/* blog */
.blog-ghost{left:0;width:1200px;top:1904px;text-align:center;font-size:62px;color:var(--faint)}
.blog-title{left:0;width:1200px;top:1980px;text-align:center;font-size:24px;text-transform:uppercase}
.blog-img{width:250px;height:186px}
.date{font-size:13px;font-weight:700;color:var(--blue)}
.post-title{font-size:20px;font-weight:700;line-height:1.35}
.post-text{font-size:15px;color:var(--muted);line-height:1.75}

/* contact */
.contact{left:0;top:2411px;width:1200px;height:622px;background:linear-gradient(160deg,#0d1a9a 0%,#0a0f6e 45%,#06094d 100%);clip-path:polygon(0 18%,100% 0,100% 100%,0 100%)}
.contact-title{left:78px;top:2600px;font-size:42px;font-weight:800;color:var(--white);line-height:1.22;text-transform:uppercase}
.contact-text{left:78px;top:2840px;width:480px;font-size:13px;color:#d8dcff;line-height:1.85}
.form{left:747px;top:2498px;width:380px;height:492px;background:var(--white)}
.field{position:absolute;left:40px;width:300px;border-bottom:1px solid #bbb;font-size:15px;padding-bottom:12px}

/* footer */
.foot-h{font-size:22px;color:#2a2a2a}
.foot-list{list-style:none;font-size:14px;line-height:2.05}
.foot-list li::before{content:"›";margin-right:22px;font-weight:700}
.foot-contact{font-size:14px;line-height:2.05}
.social{width:26px;height:26px;border-radius:50%;background:var(--blue)}
.bottom-bar{left:0;top:3360px;width:1200px;height:36px;background:var(--footer-bar);color:var(--white);font-size:13px;text-align:center;line-height:36px}
</style>
</head>
<body>
<div class="page">

<header class="abs site-header">
  <div class="abs brand">Kestrova</div>
  <nav class="abs nav">
    <span class="nav-home"><svg width="18" height="16" viewBox="0 0 18 16"><path d="M9 0 0 8h2.5v8h4.5v-5h4v5h4.5V8H18z" fill="#fff"/></svg></span>
    <span>About us</span><span>Services</span><span>Team</span><span>Blog</span><span>Contact us</span>
  </nav>
</header>

<section>
  <div class="abs hero" role="img" aria-label="Photo of an engineer in a server room with a blue network overlay"></div>
  <svg class="abs arrow" width="16" height="26" viewBox="0 0 16 26"><path d="M14 2 3 13l11 11" stroke="#fff" stroke-width="4" fill="none"/></svg>
  <svg class="abs arrow-r" width="16" height="26" viewBox="0 0 16 26"><path d="M2 2l11 11L2 24" stroke="#fff" stroke-width="4" fill="none"/></svg>
  <div class="abs hero-panel">
    <h1>WE ARE A REMOTE DBA TEAM</h1>
    <p>We offering data platform management. Sapien vestibulum non. At ut sed ligula animi nunc mauris blandit non nulla lacinia duis. Senectus ac tincidunt. Sapien commodo nulla. Pede quam sollicitudin vivamus elit porta.</p>
    <a class="btn btn-grey">Get started now ›</a>
  </div>
</section>

<section>
  <div class="abs stats"></div>
  <h2 class="abs stats-title"><b>25</b> Years of quality<br>service in remote DBA</h2>
  <svg class="abs stats-dot" viewBox="0 0 30 30"><circle cx="15" cy="15" r="15" fill="#1c22a8"/><path d="M12 9l6 6-6 6" stroke="#fff" stroke-width="2.5" fill="none"/></svg>
  <p class="abs stats-text">Duis aute irure dolor in reprehenderit in voluptate velit esse cillum dolore eu fugiat nulla pariatur. Excepteur sint occaecat cupidatat non proident, sunt in culpa qui officia deserunt mollit anim id est laborum. Consect petur adipiscing elit. eu fugiat nulla pariatur. Excepteur sint occaecat</p>
</section>

<section>
  <div class="abs ghost about-ghost">About</div>
  <h2 class="abs about-title">Remote <b>DBA</b></h2>
  <div class="abs rule" style="left:80px;top:966px"></div>
  <p class="abs about-lead">Gravida consectetuer pede laoreet ac a non leo non tellus amet vel. Magna suspendisse vestibulum.</p>
  <p class="abs about-body">Convallis curabitur vestibulum. Justo rutrum a. A ut arcu felis eget litora libero ligula morbi vestibulum eu tellus vel consectetur congue. Ultricies et commodo amet accumsan nunc eget mattis tincidunt nonummy donec viverra sed nec iaculis consectetur lectus dictum. Velit iaculis a.</p>
  <a class="abs btn btn-blue" style="left:73px;top:1183px">Read more ›</a>

  <div class="abs service" style="left:618px;top:880px">
    <svg width="48" height="44" viewBox="0 0 48 44"><rect x="4" y="4" width="40" height="32" rx="2" fill="none" stroke="#1c22a8" stroke-width="2"/><path d="M10 12h14M10 18h20M10 24h12M30 12h8" stroke="#1c22a8" stroke-width="2"/><path d="M2 40h44" stroke="#1c22a8" stroke-width="2"/></svg>
    <h3>We deliver remote database</h3>
    <p>Enim aliquam nihil. Id mauris turpis. Condimentum pellentesque urna. Sapien vestibulum non.</p>
  </div>
  <div class="abs service" style="left:898px;top:880px">
    <svg width="44" height="48" viewBox="0 0 44 48"><circle cx="22" cy="12" r="8" fill="none" stroke="#1c22a8" stroke-width="2"/><path d="M6 46V34c0-6 6-10 16-10s16 4 16 10v12" fill="none" stroke="#1c22a8" stroke-width="2"/></svg>
    <h3>Oversee the database administrators</h3>
    <p>Enim aliquam nihil. Id mauris turpis. Condimentum pellentesque</p>
  </div>
  <div class="abs service" style="left:618px;top:1058px">
    <svg width="48" height="44" viewBox="0 0 48 44"><rect x="20" y="4" width="24" height="18" fill="none" stroke="#1c22a8" stroke-width="2"/><circle cx="12" cy="14" r="6" fill="none" stroke="#1c22a8" stroke-width="2"/><path d="M2 42V32c0-5 4-8 10-8s10 3 10 8v10M2 42h44" fill="none" stroke="#1c22a8" stroke-width="2"/></svg>
    <h3>Data platform administration and development</h3>
    <p>Enim aliquam nihil. Id mauris turpis. Condimentum pellentesque</p>
  </div>
  <div class="abs service" style="left:898px;top:1050px">
    <svg width="48" height="48" viewBox="0 0 48 48"><rect x="18" y="4" width="28" height="22" fill="none" stroke="#1c22a8" stroke-width="2"/><path d="M24 18l6-6 5 4 7-7" stroke="#1c22a8" stroke-width="2" fill="none"/><circle cx="10" cy="18" r="6" fill="none" stroke="#1c22a8" stroke-width="2"/><path d="M0 46V36c0-5 4-8 10-8s10 3 10 8v10" fill="none" stroke="#1c22a8" stroke-width="2"/></svg>
    <h3>Consult and training</h3>
    <p>Enim aliquam nihil. Id mauris turpis. Condimentum pellentesque urna. Sapien vestibulum non.</p>
  </div>
</section>

<section>
  <div class="abs team" role="img" aria-label="Photo of a team meeting, tinted blue"></div>
  <div class="abs ghost team-ghost">Our team</div>
  <h2 class="abs team-title">TEAM</h2>
  <div class="abs rule" style="left:566px;top:1426px;background:#fff;width:40px"></div>
  <div class="abs portrait" style="left:348px;top:1492px;width:92px;height:92px" role="img" aria-label="Team member portrait"></div>
  <div class="abs portrait" style="left:428px;top:1480px;width:116px;height:116px" role="img" aria-label="Team member portrait"></div>
  <div class="abs portrait" style="left:530px;top:1470px;width:140px;height:140px" role="img" aria-label="Team member portrait"></div>
  <div class="abs portrait" style="left:656px;top:1480px;width:116px;height:116px" role="img" aria-label="Team member portrait"></div>
  <div class="abs portrait" style="left:756px;top:1492px;width:92px;height:92px" role="img" aria-label="Team member portrait"></div>
  <p class="abs team-text">Convallis curabitur vestibulum. Justo rutrum a. A ut arcu felis eget litora libero ligula morbi vestibulum eu tellus vel consectetur congue. Ultricies et commodo amet accumsan nunc eget mattis tincidunt nonummy donec viverra sed nec iaculis consectetur lectus dictum. Velit iaculis a.</p>
  <a class="abs btn btn-grey" style="left:528px;top:1732px;margin:0">Read more ›</a>
</section>

<section>
  <div class="abs ghost blog-ghost">Our recent post</div>
  <h2 class="abs blog-title">Our <b>Blog</b></h2>
  <div class="abs rule" style="left:566px;top:2024px;width:40px"></div>

  <div class="abs blog-img" style="left:72px;top:2082px;background:radial-gradient(circle at 50% 40%,#e8d48a 0%,#2a4fa0 25%,#08122e 70%)" role="img" aria-label="Light bulb over a circuit board"></div>
  <div class="abs date" style="left:72px;top:2284px">8-JAN-2018</div>
  <div class="abs post-title" style="left:72px;top:2312px;width:250px">Pellentesque molestie ante and consectetur...</div>

  <div class="abs blog-img" style="left:349px;top:2082px;background:linear-gradient(180deg,#1a2a5a 0%,#4a6aa8 50%,#0e1530 100%)" role="img" aria-label="Person walking through a server room aisle"></div>
  <div class="abs date" style="left:349px;top:2284px">8-JAN-2018</div>
  <div class="abs post-title" style="left:349px;top:2312px;width:250px">Integer vitaeneque vel augue malesuada...</div>

  <div class="abs date" style="left:643px;top:2090px">8-JAN-2018</div>
  <div class="abs post-title" style="left:643px;top:2110px;width:440px">Curabitur porta sapienne tortor ornare</div>
  <p class="abs post-text" style="left:643px;top:2148px;width:460px">Lorem Ipsum is simply dummy text of the printing typesetting industry. Lorem Ipsum has been the industry's standard dummy text ever since...</p>
  <a class="abs btn btn-blue" style="left:643px;top:2272px;height:42px;padding:0 26px;font-size:13px">Check all blogs</a>
</section>

<section>
  <div class="abs contact" role="img" aria-label="Dark blue background with a network line pattern"></div>
  <h2 class="abs contact-title">If you have a<br>question,<br>you can contact us.<br>Just fill a form.</h2>
  <div class="abs rule" style="left:80px;top:2820px;width:40px;background:#fff"></div>
  <p class="abs contact-text">At ut sed ligula animi nunc mauris blandit non nulla lacinia duis. Senectus ac tincidunt. Sapien commodo nulla. Pede quam sollicitudin vivamus elit porta. Etiam ut nisl vestibulum maecenas vestibulum velit suscipit porta. Mollit in pretium sollicitudin semper magna quia nibh vitae. Gravida consectetuer pede laoreet ac a non leo non tellus amet vel. Magna suspendisse vestibulum.</p>
  <form class="abs form">
    <div class="field" style="top:42px">Name</div>
    <div class="field" style="top:108px">Email</div>
    <div class="field" style="top:174px">Phone</div>
    <div class="field" style="top:240px;height:150px">Message</div>
    <span class="abs btn btn-blue" style="left:138px;top:418px">Send ›</span>
  </form>
</section>

<footer>
  <div class="abs brand" style="top:3068px;left:70px;font-size:34px">Kestrova</div>
  <p class="abs" style="left:76px;top:3142px;width:280px;font-size:13px;color:#444;line-height:1.75">Donec et varius lacinia pellentesque vivamus. Ultrices nec tincidunt. Sed libero nostra in tempor eu. Vitae mauris in elit aliquam dolor tempus ipsum libero. Non pellentesque erat. Duis erat condimentum.</p>
  <a class="abs btn btn-blue" style="left:76px;top:3272px;height:30px;padding:0 16px;font-size:11px">More ›</a>

  <h3 class="abs foot-h" style="left:437px;top:3070px;font-weight:400">Quick Links</h3>
  <div class="abs rule" style="left:437px;top:3108px;width:40px"></div>
  <ul class="abs foot-list" style="left:437px;top:3128px">
    <li>Home</li><li>About Us</li><li>Service</li><li>Team</li><li>Blog</li><li>Contact Us</li>
  </ul>

  <h3 class="abs foot-h" style="left:648px;top:3068px;font-weight:400">Contact Us</h3>
  <div class="abs rule" style="left:648px;top:3106px;width:40px"></div>
  <div class="abs foot-contact" style="left:648px;top:3128px;width:260px">
    <div>⌖ &nbsp; 9870 Lorium ipsum, Dolor amit,<br>&nbsp;&nbsp;&nbsp;&nbsp; City name, country.</div>
    <div>✆ &nbsp; +1 800 555 0142</div>
    <div>☎ &nbsp; +1 800 555 0187</div>
    <div>✉ &nbsp; hello@kestrova.cz</div>
  </div>

  <h3 class="abs foot-h" style="left:950px;top:3070px;font-weight:400">Follow Us</h3>
  <div class="abs rule" style="left:950px;top:3108px;width:40px"></div>
  <div class="abs social" style="left:952px;top:3140px" aria-label="Social link 1"></div>
  <div class="abs social" style="left:985px;top:3140px" aria-label="Social link 2"></div>
  <div class="abs social" style="left:1018px;top:3140px" aria-label="Social link 3"></div>
  <div class="abs social" style="left:1051px;top:3140px" aria-label="Social link 4"></div>
  <div class="abs social" style="left:1084px;top:3140px" aria-label="Social link 5"></div>

  <div class="abs bottom-bar">© 2018 | <b>Kestrova</b></div>
</footer>

</div>
</body>
</html>
```